Irrigation Business needs their business cards modernised and revamped

I would like to keep my current logo, colours and revamp the format of the card.

I would like the card to be clean yet important.

Im not sure if you include texture but i would like the named logo to be indented into the card etc.

show me something alive and free something thats clinical to the point yet has a feel of achievement. i would like people to go nice card.

Target Market(s)

high end clients, corporate, sports field manger, the guys that make the decisions

Industry/Entity Type

Business

Contact Information for Business Card

nformation to be included

Dean Harlow (Director)
0487305526
dean@kolvat.biz
www.kestonfieldworks.com

instagram logo
google logo
facebook logo

Colors

Designer to choose colors to be used in the design.

Requirements
Nice to have
• indentations a really nice feel to the card good texture

```html
<!DOCTYPE html>
<html lang="en">
<head>
<meta charset="utf-8">
<title>Keston Fieldworks – Business Card</title>
<link rel="stylesheet" href="https://fonts.googleapis.com/css2?family=Roboto:wght@400;700&display=swap">
<style>
  :root {
    --backdrop: #e6e6e6;
    --card: #f7f7f8;
    --card-shade: #eceef1;
    --navy: #2f4f93;
    --sky: #3a8fcb;
    --pale-blue: #aac9ea;
    --ink: #333333;
    --white: #ffffff;
    --ghost: rgba(47, 79, 147, 0.06);
  }
  * { margin: 0; padding: 0; box-sizing: border-box; }
  html, body {
    width: 1200px; height: 576px; overflow: hidden;
    background: var(--backdrop);
    font-family: "Roboto", Arial, sans-serif;
  }
  .stage { position: relative; width: 1200px; height: 576px; }
  .card {
    position: absolute; top: 138px;
    width: 485px; height: 293px;
    border-radius: 12px; overflow: hidden;
    background: linear-gradient(135deg, var(--white) 0%, var(--card) 55%, var(--card-shade) 100%);
    box-shadow: 0 3px 6px rgba(0,0,0,0.18);
  }
  .card--front { left: 82px; }
  .card--back { left: 602px; }
  .ghost-ring {
    position: absolute; border-radius: 50%;
    border: 14px solid var(--ghost);
  }
  .card--front .ghost-ring { width: 250px; height: 250px; left: 290px; top: 10px; }
  .card--back .ghost-ring { width: 230px; height: 230px; left: 345px; top: -10px; }

  .brand-mark { position: absolute; border-radius: 50%; background: var(--sky); border: 3px solid var(--navy); }
  .brand-name {
    position: absolute; color: var(--navy); font-weight: 700;
    white-space: nowrap; letter-spacing: 0.01em;
  }
  .card--front .brand-mark { width: 92px; height: 92px; left: 196px; top: 56px; }
  .card--front .brand-name { left: 0; width: 485px; text-align: center; top: 178px; font-size: 28px; }

  .front-footer { position: absolute; left: 81px; top: 264px; width: 322px; height: 16px; }
  .rule { position: absolute; top: 7px; height: 2px; width: 117px; background: var(--navy); }
  .rule--left { left: 0; }
  .rule--right { right: 0; }
  .social { position: absolute; display: flex; gap: 6px; }
  .social span { width: 16px; height: 16px; border-radius: 50%; background: var(--navy); }
  .front-footer .social { left: 131px; top: 0; }

  .card--back .brand-mark { width: 80px; height: 80px; left: 27px; top: 32px; }
  .card--back .brand-name { left: 125px; top: 58px; font-size: 25px; }
  .person { position: absolute; left: 36px; top: 140px; }
  .person__name { color: var(--navy); font-weight: 700; font-size: 20px; letter-spacing: 0.01em; }
  .person__role { color: var(--ink); font-size: 11px; margin-top: 4px; }
  .card--back .social { left: 36px; top: 196px; gap: 5px; }
  .card--back .social span { width: 19px; height: 19px; }

  .wave { position: absolute; left: 0; top: 0; width: 485px; height: 293px; }
  .contact {
    position: absolute; right: 26px; top: 217px;
    list-style: none; text-align: right;
    color: var(--white); font-size: 12.5px; line-height: 17px;
  }
  .contact li { display: flex; justify-content: flex-end; align-items: center; gap: 6px; }
  .contact svg { width: 10px; height: 10px; fill: var(--pale-blue); }
</style>
</head>
<body>
<main class="stage">
  <section class="card card--front" aria-label="Card front">
    <div class="ghost-ring"></div>
    <div class="brand-mark"></div>
    <div class="brand-name">KESTON FIELDWORKS</div>
    <div class="front-footer">
      <div class="rule rule--left"></div>
      <div class="social" aria-label="Social profiles"><span></span><span></span><span></span></div>
      <div class="rule rule--right"></div>
    </div>
  </section>

  <section class="card card--back" aria-label="Card back">
    <div class="ghost-ring"></div>
    <svg class="wave" viewBox="0 0 485 293" aria-hidden="true">
      <path d="M0 250 C 110 300, 260 240, 330 205 C 390 178, 440 168, 485 166 L485 293 L0 293 Z" fill="var(--navy)"/>
      <path d="M0 232 C 100 262, 220 248, 310 200 C 380 164, 440 152, 485 148 L485 158 C 440 162, 385 176, 318 210 C 230 256, 110 272, 0 248 Z" fill="var(--sky)"/>
      <path d="M40 262 C 140 276, 240 262, 300 236 C 250 268, 140 284, 40 262 Z" fill="var(--sky)"/>
    </svg>
    <div class="brand-mark"></div>
    <div class="brand-name">KESTON FIELDWORKS</div>
    <div class="person">
      <div class="person__name">DEAN HARLOW</div>
      <div class="person__role">Director</div>
    </div>
    <div class="social" aria-label="Social profiles"><span></span><span></span><span></span></div>
    <ul class="contact">
      <li>0487305526
        <svg viewBox="0 0 10 10" aria-hidden="true"><path d="M1 3 Q5 0 9 3 L8 4.5 L6.5 4 L6.5 3 Q5 2.5 3.5 3 L3.5 4 L2 4.5 Z M2 5 H8 V9 H2 Z"/></svg>
      </li>
      <li>dean@kolvat.biz
        <svg viewBox="0 0 10 10" aria-hidden="true"><path d="M0 2 H10 V8 H0 Z" /><path d="M0 2 L5 6 L10 2" fill="none" stroke="var(--navy)" stroke-width="1"/></svg>
      </li>
      <li>kestonfieldworks.com
        <svg viewBox="0 0 10 10" aria-hidden="true"><circle cx="5" cy="5" r="4.5"/><path d="M0.5 5 H9.5 M5 0.5 V9.5" stroke="var(--navy)" stroke-width="0.8"/></svg>
      </li>
    </ul>
  </section>
</main>
</body>
</html>
```